Birchpoint Studio Complementary Pass

I’d like a complimentary pass for any 30-minute Birchpoint Studio session. Choose one of the following options: Infrared Sauna with Red Light, Massage Chair Veltrafix Compression Therapy, or Paraffin Wax Hand Bath.

Please incorporate the logo and brand colors into your design. I’d like a square image that will be printed on square business cards (no rectangles).

Please refer to the logo and menu for more details.

Contact Information for Business Card

See discretion

```html
<!DOCTYPE html>
<html lang="en">
<head>
<meta charset="UTF-8">
<title>Birchpoint Studio Complimentary Pass</title>
<link href="https://fonts.googleapis.com/css2?family=Montserrat:ital,wght@0,400;0,500;0,700;0,800;1,400;1,700;1,800&family=Great+Vibes&family=Oswald:wght@500&display=swap" rel="stylesheet">
<style>
  :root {
    --coral: #e8664a;
    --purple: #3f2a8c;
    --lavender: #6a4fb0;
    --ink: #333336;
    --paper: #f4f4f4;
    --panel-top: #ededf0;
    --panel-bottom: #e4e4e8;
    --backdrop: #1d1d1f;
  }
  * { box-sizing: border-box; margin: 0; padding: 0; }
  html, body {
    width: 1200px;
    height: 1059px;
    overflow: hidden;
    background: var(--backdrop);
  }
  .pass {
    position: absolute;
    left: 90px;
    top: 19px;
    width: 1020px;
    height: 1020px;
    background: var(--paper);
    font-family: "Montserrat", sans-serif;
    text-align: center;
    overflow: hidden;
  }
  .pass__band {
    position: absolute;
    left: 0; top: 0;
    width: 100%;
    height: 117px;
    background: var(--coral);
  }
  .brand__dot {
    position: absolute;
    left: 467px;
    top: 72px;
    width: 86px;
    height: 86px;
    border-radius: 50%;
    background: var(--paper);
  }
  .brand__name {
    position: absolute;
    left: 0; width: 100%;
    top: 160px;
    font-size: 66px;
    font-weight: 700;
    color: var(--purple);
    letter-spacing: -1px;
    line-height: 1;
  }
  .brand__tagline {
    position: absolute;
    left: 0; width: 100%;
    top: 252px;
    font-family: "Oswald", sans-serif;
    font-weight: 500;
    font-size: 21px;
    letter-spacing: 2.5px;
    color: var(--purple);
    line-height: 1;
  }
  .pass__title {
    position: absolute;
    left: 0; width: 100%;
    top: 292px;
    font-family: "Great Vibes", cursive;
    font-weight: 400;
    font-size: 80px;
    color: var(--purple);
    line-height: 1.1;
  }
  .pass__label {
    position: absolute;
    left: 0; width: 100%;
    top: 388px;
    font-size: 48px;
    font-weight: 800;
    color: var(--coral);
    letter-spacing: 0.5px;
    line-height: 1;
  }
  .offer {
    position: absolute;
    left: 106px;
    top: 463px;
    width: 834px;
    height: 368px;
    border: 2.5px solid var(--purple);
    border-radius: 18px;
    background: linear-gradient(160deg, var(--panel-top), var(--panel-bottom));
  }
  .offer__headline {
    margin-top: 5px;
    font-size: 30px;
    font-weight: 800;
    font-style: italic;
    color: var(--purple);
    line-height: 42px;
  }
  .offer__rule {
    width: 425px;
    height: 2px;
    margin: 11px auto 0;
    background: linear-gradient(90deg, transparent, var(--coral) 30%, var(--coral) 70%, transparent);
  }
  .offer__intro {
    margin-top: 6px;
    font-size: 32px;
    font-weight: 400;
    color: var(--lavender);
    line-height: 40px;
    letter-spacing: 0.4px;
  }
  .offer__list {
    list-style: none;
    text-align: left;
    margin: 4px 0 0 120px;
  }
  .offer__item {
    position: relative;
    padding-left: 36px;
    font-size: 33px;
    font-weight: 400;
    color: var(--ink);
    line-height: 48px;
    letter-spacing: 0.3px;
  }
  .offer__item::before {
    content: "";
    position: absolute;
    left: 14px;
    top: 22px;
    width: 6px;
    height: 6px;
    border-radius: 50%;
    background: var(--coral);
  }
  .pass__terms {
    position: absolute;
    left: 0; width: 100%;
    top: 864px;
    font-size: 26px;
    font-style: italic;
    font-weight: 400;
    color: var(--ink);
    line-height: 37px;
    letter-spacing: 0.2px;
  }
</style>
</head>
<body>
  <main class="pass">
    <div class="pass__band"></div>
    <div class="brand__dot"></div>
    <div class="brand__name">corvane</div>
    <div class="brand__tagline">PHYSICAL THERAPY</div>
    <h1 class="pass__title">Birchpoint Studio</h1>
    <h2 class="pass__label">COMPLIMENTARY PASS</h2>

    <section class="offer">
      <p class="offer__headline">Enjoy any 30-minute<br>Birchpoint Studio session on us!</p>
      <div class="offer__rule"></div>
      <p class="offer__intro">Choose one of the following options:</p>
      <ul class="offer__list">
        <li class="offer__item">Infrared Sauna + Red Light</li>
        <li class="offer__item">Massage Chair</li>
        <li class="offer__item">Veltrafix Compression Therapy</li>
        <li class="offer__item">Paraffin Wax Hand Bath</li>
      </ul>
    </section>

    <p class="pass__terms">One pass per person. Not valid with any other offer.<br>For safety, a rest/cool-down period is required after 30 minutes<br>in the sauna.</p>
  </main>
</body>
</html>
```